I am looking for a modern, clean and neat design for a reflexology and well being business. The business name is Gralo Tund (this is an old Latin word for wellbeing). The colours I would like are purple, white and grey. I am open to suggestions for pictures such as healing or working hands, a pair of feet, images that represent my business that you may think of....... or maybe you think no images at all would be best? My tag line is: "Relax, Renew, Revive" or "Find you balance......... Relax, Renew, Revive" I can decide which I want so I would like to see what both would look like. I would like space on the back to write the client's appointment date and time (more than once)

```html
<!DOCTYPE html>
<html lang="en">
<head>
<meta charset="utf-8">
<title>Gralo Tund – Business Card</title>
<link rel="stylesheet" href="https://fonts.googleapis.com/css2?family=Open+Sans:wght@400;600;700&display=swap">
<style>
  :root {
    --page: #2a2a2c;
    --card-dark: #141414;
    --card-light: #ffffff;
    --purple: #9b1fc9;
    --grey: #5e5e60;
    --grey-light: #b8b8ba;
    --ink: #3a3a3c;
    --divider: #2c2c2e;
    --dots: #888888;
  }
  * { box-sizing: border-box; margin: 0; padding: 0; }
  html, body { width: 1200px; height: 900px; overflow: hidden; }
  body {
    background: var(--page);
    font-family: "Open Sans", sans-serif;
    display: flex;
    align-items: center;
    justify-content: center;
    gap: 40px;
  }
  .card {
    width: 520px;
    height: 300px;
    border-radius: 22px;
    position: relative;
    overflow: hidden;
  }

  /* Front */
  .card-front { background: var(--card-dark); display: flex; }
  .front-brand {
    width: 56%;
    display: flex;
    flex-direction: column;
    align-items: center;
    justify-content: center;
    gap: 8px;
  }
  .brand-lockup { display: flex; align-items: center; gap: 12px; }
  .brand-dot { width: 16px; height: 16px; background: var(--purple); flex: none; }
  .brand-name {
    font-weight: 600;
    font-size: 36px;
    line-height: 1.1;
    color: var(--purple);
    white-space: nowrap;
  }
  .tagline {
    font-size: 13px;
    color: var(--grey-light);
    letter-spacing: 1px;
  }
  .front-divider { width: 1px; background: var(--divider); margin: 34px 0; }
  .front-details {
    flex: 1;
    padding: 50px 0 0 22px;
    color: #f2f2f2;
    font-size: 13px;
    line-height: 1.4;
  }
  .person-name { color: var(--purple); font-size: 19px; line-height: 1.2; }
  .person-role { font-size: 13px; margin-bottom: 14px; }
  .address { margin-bottom: 12px; }
  .contact-list { list-style: none; }
  .contact-list li { display: flex; align-items: center; gap: 9px; }
  .contact-list svg { width: 11px; height: 11px; fill: var(--purple); flex: none; }

  /* Back */
  .card-back {
    background: var(--card-light);
    padding: 22px 40px 0;
    color: var(--ink);
  }
  .back-brand {
    text-align: center;
    font-weight: 600;
    font-size: 34px;
    color: var(--grey);
    line-height: 1;
  }
  .back-title {
    text-align: center;
    font-weight: 700;
    font-size: 16px;
    margin: 8px 0 10px;
  }
  .back-title .accent { color: var(--purple); }
  .field-row { display: flex; align-items: flex-end; gap: 6px; margin-bottom: 12px; }
  .field-label { color: var(--purple); font-weight: 600; font-size: 14px; line-height: 1.2; white-space: nowrap; }
  .field-line { flex: 1; border-bottom: 2px dotted var(--dots); height: 14px; }
  .field-line.short { flex: 0 0 130px; }
  .field-suffix { color: var(--purple); font-size: 11px; white-space: nowrap; }
  .notice { font-size: 13.5px; font-weight: 600; margin-top: 4px; }
  .notice .accent { color: var(--purple); }
</style>
</head>
<body>

<section class="card card-front">
  <div class="front-brand">
    <div class="brand-lockup">
      <span class="brand-dot"></span>
      <span class="brand-name">Gralo Tund</span>
    </div>
    <p class="tagline">Relax, Renew, Revive</p>
  </div>
  <div class="front-divider"></div>
  <div class="front-details">
    <p class="person-name">Marcus Hale</p>
    <p class="person-role">Managing Director</p>
    <p class="address">48 Linden Row, Fairmont<br>Westland, 204118.</p>
    <ul class="contact-list">
      <li>
        <svg viewBox="0 0 24 24"><path d="M6.6 10.8a15.1 15.1 0 0 0 6.6 6.6l2.2-2.2a1 1 0 0 1 1-.25 11.4 11.4 0 0 0 3.6.6 1 1 0 0 1 1 1V20a1 1 0 0 1-1 1A17 17 0 0 1 3 4a1 1 0 0 1 1-1h3.5a1 1 0 0 1 1 1c0 1.25.2 2.45.6 3.6a1 1 0 0 1-.25 1z"/></svg>
        <span>055-987 654 321</span>
      </li>
      <li>
        <svg viewBox="0 0 24 24"><path d="M2 5h20v14H2z"/></svg>
        <span>hello@gralotund.com</span>
      </li>
      <li>
        <svg viewBox="0 0 24 24"><path d="M10.6 13.4a1 1 0 0 1 0-1.4l4-4a1 1 0 1 1 1.4 1.4l-4 4a1 1 0 0 1-1.4 0zM8 11l-2.5 2.5a3.5 3.5 0 0 0 5 5L13 16l1.4 1.4-2.5 2.5a5.5 5.5 0 0 1-7.8-7.8L6.6 9.6zm8 2l2.5-2.5a3.5 3.5 0 0 0-5-5L11 8 9.6 6.6l2.5-2.5a5.5 5.5 0 0 1 7.8 7.8l-2.5 2.5z"/></svg>
        <span>www.gralotund.com</span>
      </li>
    </ul>
  </div>
</section>

<section class="card card-back">
  <h1 class="back-brand">Gralo Tund</h1>
  <h2 class="back-title">Your Next <span class="accent">Appointment on</span></h2>
  <div class="field-row">
    <span class="field-label">Name :</span>
    <span class="field-line"></span>
  </div>
  <div class="field-row">
    <span class="field-label">Date :</span>
    <span class="field-line short"></span>
    <span class="field-label">Time :</span>
    <span class="field-line"></span>
    <span class="field-suffix">AM / PM</span>
  </div>
  <div class="field-row">
    <span class="field-label">Date :</span>
    <span class="field-line short"></span>
    <span class="field-label">Time :</span>
    <span class="field-line"></span>
    <span class="field-suffix">AM / PM</span>
  </div>
  <div class="field-row">
    <span class="field-label">Date :</span>
    <span class="field-line short"></span>
    <span class="field-label">Time :</span>
    <span class="field-line"></span>
    <span class="field-suffix">AM / PM</span>
  </div>
  <p class="notice">If unable to keep appointment, <span class="accent">kindly give 24hrs notice.</span></p>
</section>

</body>
</html>
```